TALMORK

The business want a professional looking business card. We have a scetch we will add but want the extra upgrade, and would like more suggestions for variations of our business cards.

```html
<!DOCTYPE html>
<html lang="en">
<head>
<meta charset="utf-8">
<title>TALMORK – Business Card</title>
<link rel="stylesheet" href="https://fonts.googleapis.com/css2?family=Arimo:wght@400&display=swap">
<style>
  :root {
    --stage: #3d3d3d;
    --card: #ffffff;
    --gold-deep: #6f4f28;
    --gold-light: #a88244;
    --gold-text: #9a7236;
    --on-gold: #ffffff;
    --radius: 25px;
  }
  * { margin: 0; padding: 0; box-sizing: border-box; }
  html, body {
    width: 1200px;
    height: 1200px;
    overflow: hidden;
    background: var(--stage);
    font-family: "Arimo", Arial, sans-serif;
  }
  .canvas { position: relative; width: 1200px; height: 1200px; }

  .card {
    position: absolute;
    width: 689px;
    height: 393px;
    border-radius: var(--radius);
    background: var(--card);
    overflow: hidden;
    box-shadow: 0 2px 8px rgba(0,0,0,0.35);
  }
  .card-front { left: 266px; top: 158px; }
  .card-back  { left: 263px; top: 653px; }

  /* front: brand panel */
  .brand-panel {
    position: absolute;
    left: 0; top: 0;
    width: 326px; height: 100%;
    display: flex;
    flex-direction: column;
    align-items: center;
    justify-content: center;
    gap: 12px;
  }
  .brand-dot {
    width: 18px; height: 18px;
    border-radius: 50%;
    background: var(--gold-text);
  }
  .brand-name {
    color: var(--gold-text);
    font-size: 30px;
    letter-spacing: 8px;
    padding-left: 8px;
  }

  /* front: details panel */
  .details-panel {
    position: absolute;
    left: 326px; top: 0;
    width: 363px; height: 100%;
    background: linear-gradient(90deg, var(--gold-deep) 0%, var(--gold-light) 100%);
    color: var(--on-gold);
  }
  .wordmark {
    position: absolute;
    left: 57px; top: 72px;
    width: 224px;
    text-align: center;
  }
  .wordmark-name {
    display: block;
    font-size: 27px;
    letter-spacing: 10px;
    padding-left: 10px;
    line-height: 1;
  }
  .wordmark-tagline {
    display: block;
    margin-top: 8px;
    font-size: 8px;
    letter-spacing: 5px;
    padding-left: 5px;
  }
  .contact { position: absolute; left: 57px; top: 178px; }
  .contact-name { font-size: 20px; line-height: 24px; }
  .contact-role { font-size: 15px; line-height: 18px; margin-top: 4px; }
  .contact-phone { font-size: 15px; line-height: 18px; margin-top: 9px; }
  .contact-web { margin-top: 28px; font-size: 15px; line-height: 21px; }

  /* back */
  .back-lockup {
    position: absolute;
    left: 0; right: 0; top: 140px;
    display: flex;
    flex-direction: column;
    align-items: center;
    color: var(--gold-text);
  }
  .back-lockup .brand-dot { width: 22px; height: 22px; margin-bottom: 20px; }
  .back-name {
    font-size: 36px;
    letter-spacing: 13px;
    padding-left: 13px;
    line-height: 1;
  }
  .back-tagline {
    margin-top: 12px;
    font-size: 11px;
    letter-spacing: 8px;
    padding-left: 8px;
  }
</style>
</head>
<body>
<main class="canvas">
  <section class="card card-front" aria-label="Business card front">
    <div class="brand-panel">
      <span class="brand-dot" aria-hidden="true"></span>
      <span class="brand-name">TALMORK</span>
    </div>
    <div class="details-panel">
      <div class="wordmark">
        <span class="wordmark-name">TALMORK</span>
        <span class="wordmark-tagline">SINCE 2026</span>
      </div>
      <div class="contact">
        <p class="contact-name">Henrik Solvang Aasen</p>
        <p class="contact-role">CEO &amp; Founder</p>
        <p class="contact-phone">004791234567</p>
        <div class="contact-web">
          <p>talmork.llc@mailbox.com</p>
          <p>www.talmork.llc</p>
        </div>
      </div>
    </div>
  </section>

  <section class="card card-back" aria-label="Business card back">
    <div class="back-lockup">
      <span class="brand-dot" aria-hidden="true"></span>
      <span class="back-name">TALMORK</span>
      <span class="back-tagline">SINCE 2026</span>
    </div>
  </section>
</main>
</body>
</html>
```